30 Yr Pizzeria needs the freshest and flyest new flyer menu designed

Hiya,

Rilo's Pizza has been making beautiful love filled pizzas for close to 30 years...and we're stepping it up.

Fresh menu, Fresh messaging, we're finally making a splash with social media, and we want to tell the world to try us out

This project is to create a Landscape A4 3 x panel menu to showcase our amazing pizzas and pastas (with the super tasty side orders.

Some pointers to get going:
- This the the link to all resources for this project (logos/descriptions/prices/pics etc), it's vew only
https://files.example-share.net/folders/7qTxZ2pLm9RkW4vNc8HsJd3YbFgUa1eE?usp=sharing
- This is the 5 min video link of instructions and intro from me. If you want to nail this and win the contest, and design our super dooper menu, you need to watch this.
https://www.clipvista-demo.net/share/4a72c19e05b8d36f71e2c09d4b3a5e6f
- For more images, check out our instagram #rilospizzabramblecove
- I am keen for a quick turn around time, so we can have it ready for printing before end of November.

Any questions or issue of access, please reach out to me.

Rgds
Desmond

Target Market(s)

Families, Singles, hungry people, couples, more hungry people

Industry/Entity Type

Italian Restaurant

Font styles to use
Serif
Sans Serif

Colors
f48d91
ec1f27
f04a50
f59195
fbd4d5
0355a3
3176b5
85abd2
85acd3

Requirements
Must have
• Must - watch the vid - I explain what I want:
• https://www.clipvista-demo.net/share/4a72c19e05b8d36f71e2c09d4b3a5e6f
• And view the 3rd tab on the Google Spreadsheet called:
• https://sheets.example-share.net/spreadsheets/d/9Rtx-QpW2BzLk7YvHmNc4dJsEf8GaUo3TnXi1wPz/edit#gid=8273619450
• All the resources are in this folder:
• https://files.example-share.net/drive/u/0/folders/7qTxZ2pLm9RkW4vNc8HsJd3YbFgUa1eE?ogsrc=32
Nice to have
• Make it efficient, easy on the eye, easy to read, and choose photos that stand out and make you hungry.
• Yes I Described a lot of detail - but please, it's a general guide, if you have little additions/suggestions
Should not have
• The colour green - of any shade. Nice reds/blues/blacks/greys etc....check out our instagram and facebook if you want to get idea of personality and style.
• No hard to read cursive texts

```html
<!DOCTYPE html>
<html lang="en">
<head>
<meta charset="utf-8">
<title>Rilo's Pizza – Menu</title>
<link href="https://fonts.googleapis.com/css2?family=Roboto+Condensed:wght@400;700&family=Tinos:wght@400;700&display=swap" rel="stylesheet">
<style>
:root{
  --pink-1:#f48d91;--red:#ec1f27;--red-2:#f04a50;--pink-2:#f59195;--pink-pale:#fbd4d5;
  --blue:#0355a3;--blue-2:#3176b5;--blue-3:#85abd2;--ink:#1b2340;--white:#fff;
}
*{margin:0;padding:0;box-sizing:border-box}
html,body{width:1200px;height:933px;overflow:hidden;background:#000}
.menu{position:absolute;left:66px;top:50px;width:1068px;height:832px;overflow:hidden;
  font-family:"Roboto Condensed",sans-serif;color:var(--white)}
.panel-food{position:absolute;left:0;top:0;width:705px;height:832px;
  background:linear-gradient(180deg,#c9b79a 0%,#a88a62 25%,#7a5a3a 55%,#5a3f28 80%,#3c2a1c 100%)}
.panel-food::after{content:"";position:absolute;inset:0;
  background:radial-gradient(ellipse at 30% 60%,rgba(200,120,60,.35),transparent 60%),
  radial-gradient(ellipse at 80% 30%,rgba(240,220,190,.3),transparent 55%)}
.divider{position:absolute;left:352px;top:0;width:1px;height:832px;background:rgba(255,255,255,.55);z-index:2}
.line{position:absolute;transform:translateY(-50%);white-space:nowrap;z-index:3;text-shadow:0 0 3px rgba(0,0,0,.55)}
.band{position:absolute;height:21px;background:linear-gradient(90deg,var(--pink-pale),#f7c3c5);
  border-radius:0 16px 0 0;z-index:2;border-right:3px solid var(--pink-1)}
.head{position:absolute;transform:translateY(-50%);font-family:"Tinos",serif;font-size:22px;
  color:var(--blue);z-index:3;letter-spacing:.2px}
.n{font-size:12px;text-transform:uppercase}
.n.sub{color:var(--pink-2)}
.n.pk{color:var(--pink-2)}
.d{font-size:8px}
.intro{font-size:10.5px}
.p{font-size:12px;text-align:right;width:44px}
.p1{left:290px}
.p2{left:643px}
.c1{left:26px}.c2{left:370px}
.hl{position:absolute;height:14px;background:var(--pink-2);z-index:2}
.hl-text{color:var(--ink);text-shadow:none}
.ico{display:inline-block;width:8px;height:8px;border-radius:50%;vertical-align:middle;margin-left:3px}
.heart{color:var(--red);font-size:10px;margin-left:3px}
.veg{background:#3aa44a}
.hot{background:none;border:1.5px solid var(--pink-1)}
.star{color:#3bc0c8;font-size:10px;margin-left:2px}
.rule{position:absolute;height:1px;background:rgba(255,255,255,.7);z-index:3}
.gst-box{position:absolute;left:0;top:714px;width:352px;height:45px;background:var(--pink-pale);z-index:2}
.gst{position:absolute;left:26px;font-family:"Tinos",serif;font-size:11px;color:var(--ink);line-height:11px;top:6px}
.slash{position:absolute;left:160px;top:2px;width:2px;height:42px;background:var(--ink);transform:skewX(-18deg)}
.pay-label{position:absolute;left:218px;top:4px;font-size:8px;color:var(--ink)}
.pay{position:absolute;top:23px;font-size:13px;font-weight:700;color:var(--blue)}
.legal{position:absolute;left:0;top:759px;width:352px;height:73px;background:var(--white);z-index:2;
  padding:5px 12px 0 26px;font-size:7.4px;line-height:10.2px;color:var(--ink)}
.panel-info{position:absolute;left:705px;top:0;width:363px;height:832px;
  background:radial-gradient(ellipse at 40% 35%,#2a5ea6 0%,#123f82 45%,#0a2a5e 100%);text-align:center}
.brand{position:absolute;left:0;width:363px;font-family:"Tinos",serif;font-weight:700;color:var(--white)}
.tag{position:absolute;left:0;width:363px;top:190px;font-size:8px}
.dine{position:absolute;left:0;width:363px;top:213px;font-size:17px}
.info-h{position:absolute;left:0;width:363px;font-size:22px;text-decoration:underline;text-underline-offset:3px}
.info-t{position:absolute;left:0;width:363px;font-size:11.5px;line-height:15.5px}
.phone{position:absolute;left:76px;top:498px;font-size:58px;font-weight:700;letter-spacing:1px}
.phone-ico{position:absolute;left:37px;top:511px}
.photo{position:absolute;left:0;top:574px;width:363px;height:218px;
  background:radial-gradient(ellipse at 55% 55%,#e0a050 0%,#c5652c 35%,#8a3b1f 60%,rgba(10,42,94,0) 80%)}
.foot{position:absolute;left:0;top:792px;width:363px;height:40px;background:var(--blue-2);
  display:flex;align-items:center;justify-content:center;gap:10px;font-size:9.5px}
.foot span{display:flex;align-items:center;gap:3px}
.dot{width:11px;height:11px;border:1.5px solid var(--white);border-radius:50%;display:inline-block}
.dot.fill{background:var(--white);border-radius:2px}
</style>
</head>
<body>
<div class="menu">
  <div class="panel-food" role="img" aria-label="Softly blurred photo of a baked cheese pizza behind the menu text"></div>
  <div class="divider"></div>

  <!-- Side orders -->
  <div class="band" style="left:12px;top:20px;width:300px"></div>
  <div class="head c1" style="top:30px">TASTY SIDE ORDER</div>
  <div class="line n c1" style="top:49px">Garlic Bread</div><div class="line p p1" style="top:49px">3.95</div>
  <div class="line d c1" style="top:61px">Warm garlicky buttery goodness.</div>
  <div class="line n c1" style="top:74px">Herb Bread</div>
  <div class="line d c1" style="top:86px">Warm buttery goodness, but without the garlic breath.</div>
  <div class="hl" style="left:0;top:92px;width:302px"></div>
  <div class="line n c1 hl-text" style="top:99px">Garlic Bread/Herb Bread with Cheese <span class="heart">♥</span><span class="ico hot"></span></div><div class="line p p1" style="top:99px">4.95</div>
  <div class="line d c1" style="top:114px">Warm garlicky buttery cheesy goodness.</div>
  <div class="line n c1" style="top:126px">Garlic Crust</div><div class="line p p1" style="top:126px">9.95</div>
  <div class="line d c1" style="top:138px">Plain pizza with fresh garlic butter base and a sprinkle of cheese and herbs.</div>
  <div class="line n c1" style="top:150px">Greek Crust</div><div class="line p p1" style="top:150px">10.95</div>
  <div class="line d c1" style="top:162px">Plain pizza with fresh garlic butter base, onion, feta, olives and mozzarella cheese.</div>
  <div class="line n c1" style="top:176px">Pesto Crust</div><div class="line p p1" style="top:176px">9.95</div>
  <div class="line d c1" style="top:188px">Plain oregano/basil pesto pizza with feta, olives, roasted capsicum and mozzarella cheese.</div>
  <div class="hl" style="left:0;top:195px;width:239px"></div>
  <div class="line n c1 hl-text" style="top:202px">Crispy Triple Cheese Crust <span class="heart">♥</span><span class="star">★</span></div><div class="line p p1" style="top:202px">9.95</div>
  <div class="line d c1" style="top:216px">Thin and crispy garlic butter crust pizza with parmesan, feta and mozzarella cheese.</div>

  <!-- Pasta -->
  <div class="band" style="left:0;top:231px;width:310px"></div>
  <div class="head c1" style="top:241px">MADE TO ORDER PASTA</div>
  <div class="line intro c1" style="top:258px">Your choice of fettuccine, spaghetti or penne</div>
  <div class="line n sub c1" style="top:273px">Traditional Pasta</div><div class="line p p1" style="top:273px">14.95</div>
  <div class="line n pk c1" style="top:289px">Bolognese <span class="heart">♥</span><span class="ico hot"></span></div>
  <div class="line d c1" style="top:301px">Slow-simmered rich and savoury tomato and minced beef sauce, with</div>
  <div class="line d c1" style="top:313px">a our house blend of bolognese herbs.</div>
  <div class="line n c1" style="top:325px">Napolitana <span class="ico veg"></span></div>
  <div class="line d c1" style="top:338px">Spicy and fresh tomato sauce with onions simmered in red wine.</div>
  <div class="line n c1" style="top:350px">Funghi</div>
  <div class="line d c1" style="top:362px">A creamy garlic white wine sauce with mushrooms and shallots.</div>
  <div class="line n c1" style="top:374px">Carbonara <span class="star">★</span></div>
  <div class="line d c1" style="top:387px">Thin cut ham, a touch of garlic and fresh egg mixed into a smooth creamy sauce.</div>
  <div class="line n c1" style="top:399px">Boscaiola</div>
  <div class="line d c1" style="top:412px">Creamy garlic sauce with ham and mushrooms.</div>
  <div class="line n c1" style="top:424px">Mexicana</div>
  <div class="line d c1" style="top:437px">A spicy tomato sauce with pepperoni and onions.</div>
  <div class="line n c1" style="top:449px">Vegetarian <span class="ico veg"></span></div>
  <div class="line d c1" style="top:462px">A fresh and spicy tomato sauce with onions, capsicum and mushrooms.</div>
  <div class="line n c1" style="top:474px">Arrabiata <span class="ico veg"></span></div>
  <div class="line d c1" style="top:486px">A light but sophisticated sauce of tomato, red wine, virgin olive oil, garlic, chilli and basil.</div>
  <div class="line n sub c1" style="top:501px">Gourmet Pasta</div><div class="rule" style="left:120px;top:501px;width:168px"></div><div class="line p p1" style="top:501px">15.95</div>
  <div class="line n pk c1" style="top:515px">Chicken Boscaiola</div>
  <div class="line d c1" style="top:527px">A rich white wine cream sauce with chicken, mushrooms, onions and garlic.</div>
  <div class="line n c1" style="top:539px">Marinara</div>
  <div class="line d c1" style="top:551px">Prawns, mussels, baby octopus, garlic and fresh basil in a red wine tomato OR</div>
  <div class="line d c1" style="top:562px">a white wine cream sauce.</div>
  <div class="line n c1" style="top:574px">Tandoori</div>
  <div class="line d c1" style="top:586px">A creamy tangy tomato sauce with tandoori chicken, onions and mushrooms.</div>
  <div class="line n c1" style="top:598px">Tuna Mushroom</div>
  <div class="line d c1" style="top:610px">Creamy white wine sauce with chunks of juicy tuna, mushroom, garlic and shallots.</div>
  <div class="line n c1" style="top:622px">Pesto <span class="heart">♥</span></div>
  <div class="line d c1" style="top:634px">A creamy basil and oregano pesto, made with olive oil, garlic and Parmesan cheese,</div>
  <div class="line d c1" style="top:645px">topped with whole roasted pine nuts.</div>
  <div class="line n c1" style="top:657px">Thai Satay</div>
  <div class="line d c1" style="top:669px">Chargrilled marinated satay chicken in a creamy sauce, sprinkled with cracked peanuts.</div>
  <div class="line n c1" style="top:683px">Lasagna</div><div class="line p p1" style="top:683px">12.95</div>
  <div class="line d c1" style="top:696px">Our home-made bechamel and beef mince lasagna, topped with melting mozzarella</div>
  <div class="line d c1" style="top:706px">cheese and a pinch of herbs.</div>

  <div class="gst-box">
    <div class="gst">All Prices include GST.<br>Prices Subject to change<br>without notice</div>
    <div class="slash"></div>
    <div class="pay-label">PAYMENT GATEWAY</div>
    <div class="pay" style="left:178px">PAYWISE</div>
    <div class="pay" style="left:228px">CARDORA</div>
    <div class="pay" style="left:282px">COINLY</div>
  </div>
  <div class="legal">Base/Cheese Disclaimer- All pizzas come with mozzarella cheese and a tomato sauce base (unless we specify differently). Pizza Sizes-SML - 9", MED - 11", LRG - 13", FAM - 15" Allergies-Please tell us if you have any allergies we should be aware of. Guarantee-We put our soul into our pizzas. If for some reason your order didn't meet your expecations, let us know why. I'll refund your money and be grateful to you for trying us out. - Master Pizzaiolo Marco</div>

  <!-- Sub -->
  <div class="band" style="left:354px;top:20px;width:308px"></div>
  <div class="head c2" style="top:30px">RILO'S PIZZA SUB</div>
  <div class="line intro c2" style="top:49px">It's a pizza,</div><div class="line p p2" style="top:50px">9.95</div>
  <div class="line intro c2" style="top:62px">inside a fresh crusty roll. Cheesy, gooey, crunchy goodness.</div>
  <div class="line n c2" style="top:77px">Supreme – <span class="d" style="text-transform:none">Ham, cabanossi and pineapple.</span></div>
  <div class="line n c2" style="top:90px">Hawaiian – <span class="d" style="text-transform:none">Ham and pineapple.</span><span class="heart">♥</span><span class="ico hot"></span></div>
  <div class="line n c2" style="top:105px">Vegetarian – <span class="d" style="text-transform:none">Mushroom, capsicum and pineapple.</span></div>
  <div class="line n c2" style="top:118px">Make your own sub – <span class="d" style="text-transform:none">Choose any 3 toppings (seafood or chicken a little extra).</span></div>

  <div class="band" style="left:354px;top:130px;width:308px"></div>
  <div class="head c2" style="top:140px">GARDEN FRESH SALADS</div>
  <div class="line intro c2" style="top:162px">All salads come with Rilo's special homemade dressings</div>
  <div class="line n pk c2" style="top:177px">Greek Salad <span class="ico hot"></span><span class="ico veg"></span></div><div class="line p p2" style="top:177px">11.95</div>
  <div class="line d c2" style="top:188px">Fresh lettuce, tomatoes, kalamata olives, feta cheese, onion, cucumber</div>
  <div class="line d c2" style="top:199px">and capsicum.</div>
  <div class="line n pk c2" style="top:214px">Italian Salad <span class="ico hot"></span><span class="ico veg"></span></div><div class="line p p2" style="top:203px">10.95</div>
  <div class="line d c2" style="top:227px">Fresh lettuce, tomatoes, onion, cucumber and capsicum.</div>

  <div class="band" style="left:354px;top:236px;width:308px"></div>
  <div class="head c2" style="top:246px">SWEET DESSERT PIZZAS</div>
  <div class="line n pk c2" style="top:266px">Top Decked <span class="star">★</span></div><div class="line p p2" style="top:266px">12.95</div>
  <div class="line d c2" style="top:278px">A light caramel pizza topped with smashed melting blocks of Velvetine Top Layer.</div>
  <div class="line n pk c2" style="top:293px">Caramello Banana</div><div class="line p p2" style="top:293px">13.95</div>
  <div class="line d c2" style="top:305px">A rich golden caramel pizza with sliced banana, white and milk chocolate sprinkles.</div>

  <div class="band" style="left:354px;top:316px;width:308px"></div>
  <div class="head c2" style="top:326px">ITALIAN GELATO</div>
  <div class="line n pk c2" style="top:346px">Gelato Flavours</div><div class="rule" style="left:460px;top:346px;width:190px"></div><div class="line p p2" style="top:346px">6.50</div>
  <div class="line n pk c2" style="top:361px">Tartufo Jamaicana</div>
  <div class="line d c2" style="top:372px">Rich chocolate gelato outside dark cocoa sponge cake with a centre of chocolate,</div>
  <div class="line d c2" style="top:383px">rum and hazelnut.</div>
  <div class="line n pk c2" style="top:395px">Moca Nera</div>
  <div class="line d c2" style="top:407px">Coffee and chocolate gelato dripped with dark chocolate. Sophisticated and not too sweet.</div>
  <div class="line n pk c2" style="top:421px">Bacio D'Amore</div>
  <div class="line d c2" style="top:433px">The 'kiss of love'. Share this hazelnut gelato with a vanilla gelato heart, topped</div>
  <div class="line d c2" style="top:445px">with chopped hazelnuts.</div>
  <div class="line n c2" style="top:458px">Superior Mint</div>
  <div class="line d c2" style="top:470px">Soft vanilla gelato filled with fresh mint sauce and covered with chocolate.</div>
  <div class="line d c2" style="top:481px">An after-dinner mint in gelato form.</div>
  <div class="line n c2" style="top:494px">Passione</div>
  <div class="line d c2" style="top:506px">Passion fruit sorbet filled with passion fruit pulp and covered with milk chocolate.</div>
  <div class="line n c2" style="top:519px">Verdello Lemone D'Oro</div>
  <div class="line d c2" style="top:531px">The tangy fresh taste of the southern Mediterrean. Lemon flavoured gelato,</div>
  <div class="line d c2" style="top:542px">covered in green chocolate.</div>
  <div class="line n c2" style="top:555px">Super Mango</div>
  <div class="line d c2" style="top:568px">A unique gelato created from fresh mango pulp. The sweet taste of a tropical summer.</div>
  <div class="line n c2" style="top:580px">Lime</div>
  <div class="line d c2" style="top:593px">Zesty, tangy and fresh, with a hint of 'bite' to the sweetness, a gelato that's perfect after pizza.</div>
  <div class="line n pk c2" style="top:610px">250ml Gelato Cups</div><div class="rule" style="left:480px;top:610px;width:170px"></div><div class="line p p2" style="top:610px">7.50</div>
  <div class="line d c2" style="top:623px">Chocolate, Strawberry, Mango, Passion Fruit, Rum and Raisin, Pistachio</div>

  <div class="band" style="left:354px;top:635px;width:308px"></div>
  <div class="head c2" style="top:645px">DRINKS</div>
  <div class="line n c2" style="top:665px">Can</div><div class="line p p2" style="top:665px">3.50</div>
  <div class="line d c2" style="top:678px">Cola, Diet Cola, Cola Zero, Lemonade, Orange, Lemon Soda.</div>
  <div class="line n c2" style="top:689px">1.25L Bottle</div><div class="line p p2" style="top:689px">4.95</div>
  <div class="line d c2" style="top:701px">Cola, Diet Cola, Lemonade, Orange, Lemon Soda.</div>
  <div class="line n c2" style="top:714px">Ginger Beer</div><div class="line p p2" style="top:714px">3.95</div>
  <div class="line n c2" style="top:728px">600ml Water</div><div class="line p p2" style="top:728px">3.00</div>
  <div class="line n c2" style="top:742px">1.5L Water</div><div class="line p p2" style="top:742px">4.50</div>
  <div class="line n c2" style="top:761px">Sparkling Water 1L</div><div class="line p p2" style="top:761px">6.90</div>
  <div class="line n c2" style="top:775px">Sparkling Water 500ml</div><div class="line p p2" style="top:775px">3.90</div>
  <div class="line n c2" style="top:794px">Delivery Fee</div><div class="line p p2" style="top:794px">3.00</div>
  <div class="line n c2" style="top:808px">Delivery Fee ML</div><div class="line p p2" style="top:808px">2.00</div>

  <!-- Info panel -->
  <div class="panel-info">
    <div class="brand" style="top:38px;font-size:64px;line-height:64px">RILO'S</div>
    <div class="brand" style="top:112px;font-size:50px;line-height:50px;letter-spacing:6px">PIZZA</div>
    <div class="tag">575,724 Pizzas Made With Love, Since 1991</div>
    <div class="dine">DINE IN (BYO), TAKE AWAY &amp; DELIVERY</div>
    <div class="info-h" style="top:277px">TRADING HOURS</div>
    <div class="info-t" style="top:306px">We are open 6 nights (5-10PM) - closed Mondays<br>(except public holidays)</div>
    <div class="info-h" style="top:344px">CONVIENIENTLY LOCATED @</div>
    <div class="info-t" style="top:370px">Shop 15, Bramblecove Plaza,<br>Corner of Alder &amp; Finch Road, Bramblecove</div>
    <div class="info-h" style="top:410px">FREE DELIVERY</div>
    <div class="info-t" style="top:437px">For orders over $20. 3.00 fee applies for orders under $20.<br>Delivery between 6-10PM</div>
    <svg class="phone-ico" width="40" height="40" viewBox="0 0 40 40" aria-hidden="true">
      <circle cx="20" cy="20" r="18" fill="var(--blue-2)" stroke="#fff" stroke-width="2"/>
      <path d="M13 11c2-1 3 0 4 3s-1 3-1 4 3 5 5 6 2-1 4-1 4 2 3 4-4 3-8 0-8-7-9-10 0-5 2-6z" fill="#fff"/>
    </svg>
    <div class="phone">9000 4127</div>
    <div class="photo" role="img" aria-label="Photo of a whole pepperoni, olive and tomato pizza on a wooden board"></div>
    <div class="foot">
      <span><i class="dot"></i>www.rilospizza.example</span>
      <span><i class="dot"></i>#rilospizzabramblecove</span>
      <span><i class="dot fill"></i>rilospizzabramblecove</span>
    </div>
  </div>
</div>
</body>
</html>
```